VELMA, an e-commerce website with a twist, providing consumer-to-consumer and business-to-consumer sa

I have only uploaded 10 wire-frame pages of the website. These pages have been chosen for the different lay-outs and should give an idea of what will be needed. There are many more that I won’t upload yet, I aim to choose a winner first then there will be a high possibility that the winner will get the chance to do the design work for these later.
The design I have in mind is to keep it clean and easy with no/minimal fancy fonts and hieroglyphics. The logo is white with an orange highlight on a solid background of black, please note that the logo is white on a black background and is not a black box with white lettering, trust that makes sense. I like the idea of the top part of the website being black all the way across. I don’t see the need for more than 3 colours in the actual base website (the pictures and adverts added by users will add other colours). Although orange is the highlight colour in the logo I am open to suggestions on this, so long as the highlight colour features throughout the site.

Website width is 1220px, all pages in the PDF are 1220px

Logo font is Rezlong

The company is going to be like tradu, but much more focused on raising money for charity and humanitarian relief.

Target Market(s)

the modern era of smartphones and the sharing community

Industry/Entity Type

Business

Number of Pages Required

5+ page

Font styles to use
Sans Serif
Other font styles liked:
• rezlong

Colors
faa54b
f78f20
ffffff
000000
fbfbfb
f5f5f5

Requirements
Nice to have
• Although orange is the highlight colour in the logo I am open to suggestions on this, so long as the highlight colour features throughout the site.

```html
<!DOCTYPE html>
<html lang="en">
<head>
<meta charset="utf-8">
<title>VELMA – Home</title>
<link href="https://fonts.googleapis.com/css2?family=Comfortaa:wght@400;700&family=Roboto:wght@300;400;500;700&display=swap" rel="stylesheet">
<style>
:root{
  --orange:#f78f20;
  --orange-light:#faa54b;
  --black:#000000;
  --white:#ffffff;
  --off:#fbfbfb;
  --grey:#f5f5f5;
  --line:#dcdcdc;
  --text:#222222;
  --muted:#666666;
  --navy:#0b0b2a;
}
*{box-sizing:border-box;margin:0;padding:0}
html,body{width:761px;height:1200px;overflow:hidden}
body{position:relative;background:var(--white);font-family:"Roboto",Arial,sans-serif;color:var(--text)}
.abs{position:absolute}

/* top utility bar */
.utility{left:0;top:0;width:761px;height:22px;background:var(--orange-light);color:var(--white);font-size:8px}
.utility .links-left{left:55px;top:7px}
.utility .links-right{left:402px;top:6px}
.utility span.sep{margin:0 5px}
.utility .search{left:585px;top:0;width:124px;height:22px;background:var(--orange);padding:7px 0 0 12px}
.utility .search svg{position:absolute;right:10px;top:6px}

/* header */
.header{left:0;top:22px;width:761px;height:56px;background:var(--black)}
.logo{left:55px;top:10px;color:var(--white);font-family:"Comfortaa",sans-serif;font-weight:700;font-size:28px;letter-spacing:-1px}
.nav{right:56px;top:24px;display:flex;gap:22px;color:var(--white);font-size:10px;font-weight:300}

/* hero row */
.video{width:207px;background:linear-gradient(135deg,#6b5a44,#c9b59a 55%,#3b3024)}
.video .play{left:88px;width:30px;height:30px;border-radius:50%;background:rgba(60,60,60,.75)}
.video .play::after{content:"";position:absolute;left:12px;top:8px;border-left:10px solid var(--white);border-top:7px solid transparent;border-bottom:7px solid transparent}
.video .bar{left:0;bottom:0;width:207px;height:16px;background:rgba(0,0,0,.85)}
.video .bar i{position:absolute;left:35px;top:7px;width:125px;height:3px;background:#2a5d8a}
.video .bar i::before{content:"";position:absolute;left:0;top:0;width:35px;height:3px;background:#43a6e8}
.video .bar b{position:absolute;left:10px;top:4px;border-left:7px solid var(--white);border-top:4px solid transparent;border-bottom:4px solid transparent}

.finder{left:277px;top:105px;width:208px;height:245px;background:var(--off);border:2px solid #e2e2e2}
.field{position:absolute;height:30px;background:var(--white);border:1px solid var(--line);font-family:"Comfortaa",sans-serif;font-size:10px;color:#333;padding:9px 10px}
.label{position:absolute;font-family:"Comfortaa",sans-serif;font-size:10px;color:#333}
.help{position:absolute;width:10px;height:10px;border-radius:50%;background:#333;color:var(--white);font-size:7px;font-weight:700;text-align:center;line-height:10px}
.btn-search{position:absolute;left:34px;top:196px;width:126px;height:30px;border-radius:15px;background:var(--orange);color:var(--white);font-family:"Comfortaa",sans-serif;font-weight:700;font-size:13px;text-align:center;line-height:30px}

.card{left:498px;width:208px;height:74px;border:1px solid #e6e6e6;background:var(--white)}
.card .thumb{position:absolute;left:0;top:0;width:68px;height:72px}
.card h3{position:absolute;left:77px;top:12px;font-family:"Comfortaa",sans-serif;font-size:8px;font-weight:700}
.card p{position:absolute;left:77px;top:25px;width:124px;font-size:5.6px;line-height:8.5px;color:var(--muted)}
.card a{position:absolute;left:77px;top:56px;font-size:5.5px;color:var(--orange);text-decoration:none}

/* banners */
.banner-one{left:58px;top:375px;width:648px;height:103px;background:linear-gradient(90deg,#2b2b35 0%,#53535e 25%,#121236 55%,var(--navy) 100%)}
.banner-one .watch{left:80px;top:0;width:130px;height:103px;background:radial-gradient(ellipse at 50% 50%,#3a3f48,#15171c 70%,transparent 72%)}
.banner-title{color:var(--white);font-family:"Comfortaa",sans-serif;font-weight:700;font-size:19px}
.banner-sub{color:var(--white);font-size:9px}

/* feedback */
.feedback{left:0;top:488px;width:761px;height:192px;background:var(--grey)}
.section-title{font-family:"Comfortaa",sans-serif;font-weight:700;font-size:17px;color:var(--black)}
.avatar{width:57px;height:57px;border-radius:50%;background:radial-gradient(circle,#b6a79a,#6d6158)}
.quote{position:relative;width:194px;padding-left:10px;font-size:7.4px;line-height:13.6px;color:#555;text-align:justify}
.quote .open{position:absolute;left:0;top:-3px}
.mark{color:var(--orange);font-size:10px;font-weight:700}
.role{font-family:"Comfortaa",sans-serif;font-size:8px;font-weight:700;color:#222;padding-left:10px}

.banner-two{left:54px;top:688px;width:652px;height:103px;background:linear-gradient(90deg,#241414 0%,#3c2424 45%,#8c7c70 75%,#2c1f1c 100%)}

/* charities */
.charity{width:128px;height:49px;background:var(--white);border:2px solid #e6e6e6;display:flex;align-items:center;justify-content:center;font-size:12px;font-weight:400;color:#444}

.ad{left:367px;width:333px;border:1px solid #ccc}
.ad-one{top:826px;height:108px;background:linear-gradient(90deg,#2a2a2a 0%,#f3b13a 22%,#ffffff 50%,#ffffff 100%)}
.ad-two{top:941px;height:107px;background:linear-gradient(110deg,#1f2d33 0%,#c6273a 30%,#e9e9e9 55%,#ffffff 85%,#1c3a40 100%)}

/* footer */
.footer{left:0;top:1094px;width:761px;height:106px;background:#111}
.footer .links{left:0;top:30px;width:761px;text-align:center;color:var(--white);font-size:7.5px}
.footer .links span{margin:0 4px}
.socials{left:319px;top:49px;display:flex;gap:5px}
.socials i{width:16px;height:16px;border-radius:50%;border:1px solid #9a9a9a}
.footer .copy{left:0;top:75px;width:761px;text-align:center;color:var(--white);font-size:7.5px}
.footer .code{left:725px;top:75px;color:var(--white);font-size:8px}
</style>
</head>
<body>

<div class="abs utility">
  <div class="abs links-left">Notifications<span class="sep">|</span>News<span class="sep">|</span>List Item</div>
  <div class="abs links-right">Contact Us<span class="sep">|</span>Help<span class="sep">|</span>Terms and Conditions</div>
  <div class="abs search">search
    <svg width="9" height="9" viewBox="0 0 10 10"><circle cx="4" cy="4" r="3" fill="none" stroke="#fff" stroke-width="1.6"/><line x1="6.3" y1="6.3" x2="9" y2="9" stroke="#fff" stroke-width="1.8"/></svg>
  </div>
</div>

<header class="abs header">
  <div class="abs logo">VELMA</div>
  <nav class="abs nav"><span>SHOPPING BASKET</span><span>WISH LIST</span><span>SIGN IN</span><span>MY ACCOUNT</span><span>MY RECENT SEARCHES</span></nav>
</header>

<div class="abs video" style="left:55px;top:106px;height:120px" role="img" aria-label="Video still of a laptop on a café table">
  <div class="abs play" style="top:37px"></div>
  <div class="abs bar"><b></b><i></i></div>
</div>
<div class="abs video" style="left:55px;top:232px;height:118px;background:linear-gradient(135deg,#d8d2c6,#a48e74 50%,#4a3d30)" role="img" aria-label="Video still of a man working on a laptop">
  <div class="abs play" style="top:37px"></div>
  <div class="abs bar"><b></b><i></i></div>
</div>

<form class="abs finder">
  <div class="field" style="left:17px;top:24px;width:162px">item</div><div class="help" style="left:184px;top:34px">?</div>
  <div class="field" style="left:17px;top:64px;width:162px">location</div><div class="help" style="left:184px;top:74px">?</div>
  <div class="label" style="left:20px;top:115px">from</div>
  <div class="field" style="left:51px;top:104px;width:128px"></div><div class="help" style="left:184px;top:114px">?</div>
  <div class="label" style="left:24px;top:155px">to</div>
  <div class="field" style="left:51px;top:145px;width:128px"></div><div class="help" style="left:184px;top:155px">?</div>
  <div class="btn-search">search</div>
</form>

<article class="abs card" style="top:116px">
  <div class="thumb" role="img" aria-label="Photo of a wristwatch on a suit sleeve" style="background:linear-gradient(135deg,#3a4450,#9aa3ab 50%,#1a1f25)"></div>
  <h3>dolorem ipsum quia</h3>
  <p>Lorem Ipsum has been the industry's standard dummy text ever since the 1500s, when an unknown printer took a galley of type</p>
  <a>Read More »</a>
</article>
<article class="abs card" style="top:197px">
  <div class="thumb" role="img" aria-label="Photo of hands typing on a laptop" style="background:linear-gradient(135deg,#e8d8d6,#c8485a 50%,#3a3a3a)"></div>
  <h3>porro quisquam est qui</h3>
  <p>It has survived not only five centuries, but also the leap into electronic typesetting, remaining essentially unchanged. It was popularised</p>
  <a>Read More »</a>
</article>
<article class="abs card" style="top:277px">
  <div class="thumb" role="img" aria-label="Photo of a leather strap wristwatch" style="background:linear-gradient(135deg,#8c8276,#b07a3e 50%,#2b2622)"></div>
  <h3>dolorem ipsum quia dolor</h3>
  <p>The industry's standard dummy text ever since the 1500s, when an unknown printer took a galley of type and scrambled</p>
  <a>Read More »</a>
</article>

<section class="abs banner-one">
  <div class="abs watch" role="img" aria-label="Photo of a smartwatch showing the time"></div>
  <div class="abs banner-title" style="left:341px;top:33px">neque porro quisquam est</div>
  <div class="abs banner-sub" style="left:342px;top:62px">Dolorem ipsum quia dolor sit amet, consectetur, adipisci velit</div>
</section>

<section class="abs feedback">
  <h2 class="abs section-title" style="left:310px;top:30px">user feedback</h2>
  <div class="abs avatar" style="left:74px;top:82px" role="img" aria-label="Portrait of a customer"></div>
  <div class="abs" style="left:144px;top:88px">
    <p class="quote"><span class="mark open">“</span>It is a long established fact that a reader will be distracted by the readable content of a page when looking at its layout. The point of using Lorem Ipsum <span class="mark">”</span></p>
    <p class="role" style="margin-top:6px">ceo+ insurance brokerage</p>
  </div>
  <div class="abs avatar" style="left:413px;top:82px" role="img" aria-label="Portrait of a customer"></div>
  <div class="abs" style="left:484px;top:88px">
    <p class="quote"><span class="mark open">“</span>It is a long established fact that a reader will be distracted by the readable content of a page when looking at its layout. The point of using Lorem Ipsum <span class="mark">”</span></p>
    <p class="role" style="margin-top:6px">ceo+ information technology consultancy</p>
  </div>
</section>

<section class="abs banner-two" role="img" aria-label="Photo of a chronograph wristwatch">
  <div class="abs banner-title" style="left:33px;top:30px">dolorem ipsum quia dolor</div>
  <div class="abs banner-sub" style="left:34px;top:59px">Neque porro quisquam est qui dolorem ipsum quia dolor</div>
</section>

<h2 class="abs section-title" style="left:60px;top:828px">charities supported</h2>
<div class="abs charity" style="left:54px;top:868px">Harbour Trust</div>
<div class="abs charity" style="left:193px;top:868px">Open Hands</div>
<div class="abs charity" style="left:54px;top:933px">Kindle Relief</div>
<div class="abs charity" style="left:193px;top:933px">Seedline</div>
<div class="abs charity" style="left:54px;top:998px">Amberfield Aid</div>
<div class="abs charity" style="left:193px;top:998px">Tidewater</div>

<div class="abs ad ad-one" role="img" aria-label="Advert banner with a city photo in a yellow ring"></div>
<div class="abs ad ad-two" role="img" aria-label="Advert banner with red and dark diagonal shapes"></div>

<footer class="abs footer">
  <div class="abs links">About velma <span>|</span> Safety hub <span>|</span> Resoution hub <span>|</span> Vendor hub <span>|</span> Partner hub <span>|</span> Charity hub</div>
  <div class="abs socials"><i></i><i></i><i></i><i></i><i></i><i></i></div>
  <div class="abs copy">Copyright © 2017&nbsp; All Rights Reserved</div>
  <div class="abs code">C6</div>
</footer>

</body>
</html>
```